Casino with the 'highest winning percentage' needs a stationery design

This is for a casino in Colombo, Sri Lanka and we need a stationery design for business card, letter head and envelope.

Should be very professional, simple and elegant without fancy fonts

Reason: Not fully satisfied with the designs. Need more designs.

Business

• 1. card deck symbol 'CLUBS' in red, or black

2. name in BLOCK CAPITAL LETTERS

3. Preferred font colours are black, white or red

4. Prefer 'professional /elegant' fonts
• SHOULD NOT HAVE ANY OTHER SYMBOL EXCEPT 'CLUBS'

DO NOT PREFER ITALIC FONTS

```html
<!DOCTYPE html>
<html lang="en">
<head>
<meta charset="utf-8">
<title>Corwin's Entertainment – Business Card</title>
<link rel="stylesheet" href="https://fonts.googleapis.com/css2?family=Questrial&family=Didact+Gothic&display=swap">
<style>
  :root {
    --stage: #1c1c1e;
    --card-white: #f4f4f4;
    --ink-dark: #2a2a2a;
    --ink-grey: #6e6e6e;
    --accent-red: #a5121c;
    --back-black: #0c0c0c;
    --back-red: #8e1016;
    --frame-line: #d8d8d8;
  }
  * { box-sizing: border-box; margin: 0; padding: 0; }
  html, body {
    width: 1200px; height: 890px; overflow: hidden;
    background: var(--stage);
    font-family: "Questrial", "Didact Gothic", sans-serif;
  }
  .stage { position: relative; width: 1200px; height: 890px; }

  .card-front {
    position: absolute; left: 300px; top: 60px;
    width: 600px; height: 343px;
    background: linear-gradient(135deg, #ffffff 0%, var(--card-white) 60%, #e6e6e6 100%);
    border-radius: 26px;
    color: var(--ink-dark);
  }
  .brand {
    position: absolute; left: 48px; top: 46px;
    display: flex; align-items: center; gap: 16px;
    color: var(--ink-dark);
  }
  .brand-dot { width: 44px; height: 44px; border-radius: 50%; background: var(--accent-red); }
  .brand-name { font-size: 30px; letter-spacing: 2px; line-height: 1; text-align: center; }
  .brand-name span { display: block; }
  .brand-name .sub { font-size: 15px; letter-spacing: 2.5px; margin-top: 6px; }
  .brand-name .place { font-size: 11px; letter-spacing: 3px; margin-top: 4px; }

  .company-address {
    position: absolute; right: 250px; top: 222px;
    text-align: right; font-size: 15px; line-height: 1.3; color: var(--ink-dark);
  }
  .person { position: absolute; left: 392px; top: 138px; }
  .person-name { font-family: "Didact Gothic", sans-serif; font-weight: 700; font-size: 17px; letter-spacing: 1.5px; color: var(--ink-grey); font-weight: bold; }
  .person-role { font-size: 13px; color: var(--ink-grey); margin-top: 2px; letter-spacing: .5px; }
  .contact { position: absolute; left: 392px; top: 222px; font-size: 14px; line-height: 1.35; color: var(--ink-grey); letter-spacing: .4px; }

  .card-back {
    position: absolute; top: 470px;
    width: 520px; height: 297px;
    border-radius: 24px;
  }
  .card-back.black { left: 60px; background: var(--back-black); }
  .card-back.red { left: 620px; background: var(--back-red); }
  .card-back .frame {
    position: absolute; inset: 16px;
    border: 2px solid var(--frame-line);
    border-radius: 14px;
  }
  .card-back .pattern {
    position: absolute; inset: 24px;
    border-radius: 10px;
  }
  .black .pattern { background: radial-gradient(circle, #3a3a3a 0%, #1a1a1a 100%); }
  .red .pattern { background: radial-gradient(circle, #c04048 0%, #8a1218 100%); }
</style>
</head>
<body>
<main class="stage">
  <section class="card-front">
    <div class="brand">
      <div class="brand-dot"></div>
      <div class="brand-name">
        <span>CORWIN'S</span>
        <span class="sub">ENTERTAINMENT</span>
        <span class="place">SRI LANKA</span>
      </div>
    </div>
    <div class="company-address">
      CORWIN'S LIMITED<br>
      12, Lotus Garden Road<br>
      Colombo 00300, Sri Lanka
    </div>
    <div class="person">
      <div class="person-name">DANIEL ASHFORD</div>
      <div class="person-role">General Manager</div>
    </div>
    <div class="contact">
      Tel: + 94 11 2468013<br>
      Fax: + 94 11 2468014<br>
      www.corwinscolombo.com
    </div>
  </section>

  <section class="card-back black">
    <div class="frame"></div>
    <div class="pattern" role="img" aria-label="Repeating white outline card-suit pattern on black"></div>
  </section>

  <section class="card-back red">
    <div class="frame"></div>
    <div class="pattern" role="img" aria-label="Repeating white outline card-suit pattern on red"></div>
  </section>
</main>
</body>
</html>
```